Local fast-growing company in the service sector

We are looking for a modern business card design, which should also appear on our letterheads

Target Market(s)

Private and industrial sectors

Contact Information for Business Card

Vorname Name
Kellberger Str. 18
71398 Kellbach
Tel.: 07146-839214-0
Name@agentur-kvtl.de

Colors
9d9d9d
919191
aaaaaa

Requirements
Must have
• The logo (file) in silver

```html
<!DOCTYPE html>
<html lang="de">
<head>
<meta charset="utf-8">
<title>KVTL Visitenkarte</title>
<link href="https://fonts.googleapis.com/css2?family=Open+Sans:wght@400;600;700&display=swap" rel="stylesheet">
<style>
  :root {
    --stage: #2b2b2b;
    --card-dark: #1b1b1c;
    --silver: #aaaaaa;
    --silver-mid: #9d9d9d;
    --silver-deep: #919191;
    --white: #ffffff;
    --panel-edge: #d6d6d6;
  }
  html, body {
    margin: 0;
    padding: 0;
    width: 1200px;
    height: 900px;
    overflow: hidden;
    background: var(--stage);
    font-family: "Open Sans", Arial, sans-serif;
  }
  .canvas {
    position: relative;
    width: 1200px;
    height: 900px;
  }
  .card {
    position: absolute;
    left: 300px;
    width: 600px;
    height: 343px;
    overflow: hidden;
    box-shadow: 0 10px 30px rgba(0,0,0,0.45);
  }
  .card-back {
    top: 70px;
    background: var(--card-dark);
  }
  .brand {
    position: absolute;
    display: flex;
    align-items: center;
    gap: 14px;
  }
  .brand-mark {
    width: 34px;
    height: 34px;
    background: var(--silver);
  }
  .brand-name {
    font-weight: 700;
    font-size: 52px;
    letter-spacing: 2px;
    line-height: 1;
  }
  .card-back .brand {
    left: 0;
    right: 0;
    top: 110px;
    justify-content: center;
  }
  .card-back .brand-name { color: var(--silver); }
  .card-back .website {
    position: absolute;
    left: 0;
    right: 0;
    top: 242px;
    text-align: center;
    color: var(--white);
    font-size: 13px;
    letter-spacing: 7px;
  }
  .card-front {
    top: 487px;
    background: var(--silver);
  }
  .front-panel {
    position: absolute;
    inset: 0;
  }
  .card-front .brand {
    left: 350px;
    top: 120px;
  }
  .card-front .brand-mark { width: 28px; height: 28px; }
  .card-front .brand-name { color: var(--silver-deep); font-size: 44px; }
  .contact {
    position: absolute;
    left: 50px;
    top: 200px;
    color: var(--white);
    font-size: 14px;
    line-height: 20px;
  }
  .contact-name {
    font-weight: 700;
    font-size: 14px;
    margin: 0 0 8px;
    letter-spacing: 0.5px;
  }
  .contact p { margin: 0; }
  .contact-line {
    display: flex;
    align-items: center;
    gap: 8px;
  }
  .contact-line svg { width: 12px; height: 12px; flex: none; }
</style>
</head>
<body>
<div class="canvas">

  <section class="card card-back">
    <div class="brand">
      <span class="brand-mark"></span>
      <span class="brand-name">KVTL</span>
    </div>
    <div class="website">www.agentur-kvtl.de</div>
  </section>

  <section class="card card-front">
    <svg class="front-panel" viewBox="0 0 600 343" width="600" height="343" aria-hidden="true">
      <path d="M320 0 L600 0 L600 293 L394 293 Q352 293 348 256 L317 32 Q315 10 320 0 Z"
            fill="var(--panel-edge)"/>
      <path d="M331 0 L600 0 L600 283 L397 283 Q362 283 358 252 L328 34 Q326 12 331 0 Z"
            fill="var(--white)"/>
    </svg>
    <div class="brand">
      <span class="brand-mark"></span>
      <span class="brand-name">KVTL</span>
    </div>
    <div class="contact">
      <p class="contact-name">JONAS WEBER</p>
      <p>Kellberger Str. 18</p>
      <p>71398 Kellbach</p>
      <p class="contact-line">
        <svg viewBox="0 0 12 12"><path d="M2 1 L4.5 1 L5.5 3.8 L4 5 Q5 7.5 7 8 L8.2 6.5 L11 7.5 L11 10 Q6 11.5 2.5 7 Q0.5 4 2 1 Z" fill="var(--white)"/></svg>
        07146-839214-0
      </p>
      <p class="contact-line">
        <svg viewBox="0 0 12 12"><rect x="0.5" y="2" width="11" height="8" fill="var(--white)"/><path d="M0.5 2 L6 6.5 L11.5 2" fill="none" stroke="var(--silver)" stroke-width="1"/></svg>
        Name@agentur-kvtl.de
      </p>
      <p class="contact-line">
        <svg viewBox="0 0 12 12"><circle cx="6" cy="6" r="5.5" fill="var(--white)"/><path d="M0.5 6 H11.5 M6 0.5 Q2.5 6 6 11.5 M6 0.5 Q9.5 6 6 11.5" fill="none" stroke="var(--silver)" stroke-width="0.8"/></svg>
        www.agentur-kvtl.de
      </p>
    </div>
  </section>

</div>
</body>
</html>
```